jQuery Mobile CSS for web app

Task Outline:
Create jQuery Mobile themeroller compliant CSS and icons for a mobile web app.
Task Description:
Brindle Solutions are in the process of implementing a new, web based version of their Tessel operations platform.
The web based version of Tessel is built on top of the jQuery Mobile platform and we are looking for a designer to create a jQuery Mobile themeroller compliant CSS theme pack that we can plug into our application. The aim is to remove the standard jQuery Mobile look and feel and to introduce the Brindle branding throughout the new web app.
A number of screenshots are shown in the attached design spec (brindle_solutions.pdf) that show what the current (Windows Mobile 6.5) application looks like, alongside the development version of our new web app.
Deliverables:
• jQuery Mobile (v 1.4.2) themeroller compliant CSS which provides theming for all jQuery Mobile UI components.
• Example html showing how to use the CSS theme (especially where additional html/css classes are required).
• New set of status icons (as listed in attachment)
Inspiration:
See our website for current branding: www.brindle-solutions-demo.net

```html
<!DOCTYPE html>
<html lang="en">
<head>
<meta charset="utf-8">
<title>Labor</title>
<link rel="stylesheet" href="https://fonts.googleapis.com/css2?family=Mulish:wght@400;500;700;800&family=Open+Sans:wght@400&display=swap">
<style>
  :root {
    --page-bg: #e9e9ea;
    --status-bg: #545556;
    --status-text: #ffffff;
    --brand-red: #e0101c;
    --brand-red-dark: #c20510;
    --brand-red-light: #ef2a33;
    --row-bg-top: #ffffff;
    --row-bg-bottom: #f6f6f6;
    --row-divider: #dcdcdc;
    --title-text: #4a4a4a;
    --meta-text: #707070;
    --avatar-tone: #c9c9c9;
    --footer-btn: #ffffff;
    --footer-btn-alt: #ececec;
    --footer-text: #3a3a3a;
  }
  * { box-sizing: border-box; margin: 0; padding: 0; }
  html, body {
    width: 853px; height: 1200px; overflow: hidden;
    background: var(--page-bg);
  }
  .app-screen {
    position: absolute; left: 26px; top: 0;
    width: 801px; height: 1200px;
    display: flex; flex-direction: column;
    background: #ffffff;
    font-family: "Mulish", sans-serif;
  }
  .status-bar {
    height: 43px; flex: none;
    background: var(--status-bg);
    color: var(--status-text);
    font-family: "Open Sans", sans-serif;
    font-size: 20px;
    display: flex; align-items: center; justify-content: space-between;
    padding: 0 14px;
    position: relative;
  }
  .status-bar .signal { display: flex; align-items: center; gap: 8px; }
  .status-bar .clock {
    position: absolute; left: 50%; transform: translateX(-50%);
  }
  .status-bar .battery { display: flex; align-items: center; gap: 8px; }
  .page-header {
    height: 130px; flex: none;
    background: linear-gradient(180deg, var(--brand-red-light) 0%, var(--brand-red) 45%, var(--brand-red-dark) 100%);
    display: flex; align-items: center; justify-content: center;
  }
  .page-title {
    color: #ffffff; font-weight: 700; font-size: 54px; letter-spacing: 0.5px;
  }
  .crew-list { list-style: none; flex: none; }
  .crew-item {
    height: 184px;
    display: flex; align-items: center;
    background: linear-gradient(180deg, var(--row-bg-top) 40%, var(--row-bg-bottom) 100%);
    border-bottom: 2px solid var(--row-divider);
    padding-left: 61px;
  }
  .crew-avatar {
    width: 101px; height: 118px; flex: none;
    background: var(--avatar-tone);
    border-radius: 12px;
  }
  .crew-text { margin-left: 40px; }
  .crew-role {
    color: var(--title-text); font-size: 38px; font-weight: 500; line-height: 1.1;
  }
  .crew-note {
    color: var(--meta-text); font-family: "Open Sans", sans-serif;
    font-size: 28px; margin-top: 14px;
  }
  .list-spacer { flex: 1; }
  .page-footer {
    height: 88px; flex: none;
    display: flex;
    border-top: 2px solid var(--row-divider);
  }
  .nav-btn {
    flex: 1; display: flex; align-items: center; justify-content: center; gap: 12px;
    color: var(--footer-text); font-size: 36px; font-weight: 500;
    text-decoration: none;
  }
  .nav-btn.back { background: var(--footer-btn); }
  .nav-btn.next { background: linear-gradient(180deg, #f4f4f4, var(--footer-btn-alt)); border-left: 2px solid var(--row-divider); }
</style>
</head>
<body>
<main class="app-screen">
  <div class="status-bar">
    <span class="signal">
      <svg width="30" height="18" viewBox="0 0 30 18" aria-hidden="true">
        <rect x="0" y="13" width="5" height="5" fill="#fff"/>
        <rect x="8" y="9" width="5" height="9" fill="#fff"/>
        <rect x="16" y="5" width="5" height="13" fill="#fff"/>
        <rect x="24" y="0" width="5" height="18" fill="#fff"/>
      </svg>
      3G
    </span>
    <span class="clock">8:33 PM</span>
    <span class="battery">
      99%
      <svg width="46" height="22" viewBox="0 0 46 22" aria-hidden="true">
        <rect x="1" y="1" width="40" height="20" rx="3" fill="none" stroke="#fff" stroke-width="2"/>
        <rect x="4" y="4" width="34" height="14" fill="#fff"/>
        <rect x="42" y="7" width="3" height="8" fill="#fff"/>
      </svg>
    </span>
  </div>

  <header class="page-header">
    <h1 class="page-title">Labor</h1>
  </header>

  <ul class="crew-list">
    <li class="crew-item">
      <div class="crew-avatar" role="img" aria-label="Worker with hard hat icon"></div>
      <div class="crew-text">
        <p class="crew-role">2 x Field Foreman</p>
        <p class="crew-note">Etiam nunc venenatis n tristique</p>
      </div>
    </li>
    <li class="crew-item">
      <div class="crew-avatar" role="img" aria-label="Worker with hard hat icon"></div>
      <div class="crew-text">
        <p class="crew-role">1 x Master Electrician</p>
        <p class="crew-note">Etiam nunc venenatis n tristique</p>
      </div>
    </li>
    <li class="crew-item">
      <div class="crew-avatar" role="img" aria-label="Worker with hard hat icon"></div>
      <div class="crew-text">
        <p class="crew-role">2 x&nbsp; Field Supervisor</p>
        <p class="crew-note">Etiam nunc venenatis n tristique</p>
      </div>
    </li>
    <li class="crew-item">
      <div class="crew-avatar" role="img" aria-label="Worker with hard hat icon"></div>
      <div class="crew-text">
        <p class="crew-role">10 x Pusher</p>
        <p class="crew-note">Etiam nunc venenatis n tristique</p>
      </div>
    </li>
  </ul>

  <div class="list-spacer"></div>

  <nav class="page-footer">
    <a class="nav-btn back" href="#">
      <svg width="40" height="40" viewBox="0 0 40 40" aria-hidden="true">
        <circle cx="20" cy="20" r="17" fill="none" stroke="#3a3a3a" stroke-width="4"/>
        <path d="M11 20 L19 12 L19 17 L29 17 L29 23 L19 23 L19 28 Z" fill="#3a3a3a"/>
      </svg>
      Back
    </a>
    <a class="nav-btn next" href="#">
      Next
      <svg width="40" height="40" viewBox="0 0 40 40" aria-hidden="true">
        <circle cx="20" cy="20" r="17" fill="none" stroke="#3a3a3a" stroke-width="4"/>
        <path d="M29 20 L21 12 L21 17 L11 17 L11 23 L21 23 L21 28 Z" fill="#3a3a3a"/>
      </svg>
    </a>
  </nav>
</main>
</body>
</html>
```